business card for a massage therapy practice named 'Cedar and Willow Massage Studio'

I really need a trendy, yet easy on the eyes business card to complement my logo. Ideally with some gold or rose gold foil work.

My uploaded file of the logo I have in horizontal but I have a vertical version as well. Another color that is used in the website is a blush pink here and there. I'd like to see some trendy tropical leaves in the design.

```html
<!DOCTYPE html>
<html lang="en">
<head>
<meta charset="utf-8">
<title>Cedar and Willow Massage Studio – Business Card</title>
<link rel="stylesheet" href="https://fonts.googleapis.com/css2?family=Open+Sans:wght@400;600&display=swap">
<style>
  :root {
    --stage: #141414;
    --card: #1e1e1e;
    --card-edge: #262626;
    --ink: #f4f4f4;
    --mint: #72d6b8;
    --gold: #b49a5e;
    --rule: #555555;
    --muted: #cfcfcf;
    --ghost: rgba(255,255,255,0.05);
  }
  * { margin: 0; padding: 0; box-sizing: border-box; }
  html, body { width: 1200px; height: 900px; overflow: hidden; }
  body {
    background: var(--stage);
    font-family: "Open Sans", Arial, sans-serif;
    color: var(--ink);
    position: relative;
  }
  .card {
    position: absolute;
    width: 620px;
    height: 354px;
    background: var(--card);
    border-radius: 22px;
    box-shadow: 0 18px 40px rgba(0,0,0,0.6);
    overflow: hidden;
  }
  .card--back { left: 130px; top: 70px; }
  .card--front { left: 450px; top: 476px; }

  .leaf-decor {
    position: absolute;
    left: -60px;
    top: 40px;
    width: 230px;
    height: 230px;
    border-radius: 50%;
    background: var(--ghost);
  }

  .brand {
    position: absolute;
    display: flex;
    align-items: center;
    gap: 16px;
  }
  .brand__mark {
    width: 44px; height: 44px;
    border-radius: 50%;
    background: var(--gold);
    flex: none;
  }
  .brand__name {
    font-weight: 600;
    font-size: 24px;
    line-height: 1.2;
    color: var(--ink);
    letter-spacing: 0.5px;
  }

  /* back */
  .card--back .brand { left: 150px; top: 96px; }
  .follow {
    position: absolute;
    left: 180px; right: 40px;
    top: 222px;
    text-align: center;
  }
  .follow__rule { height: 1px; background: var(--rule); }
  .follow__label {
    font-size: 11px;
    letter-spacing: 1.5px;
    color: var(--muted);
    margin: 10px 0 6px;
  }
  .follow__links { display: flex; justify-content: center; gap: 6px; margin-bottom: 14px; }
  .follow__dot { width: 16px; height: 16px; border-radius: 50%; background: #5a6f8f; }

  /* front */
  .card--front .brand { left: 250px; top: 62px; }
  .divider {
    position: absolute;
    left: 250px; right: 30px; top: 150px;
    height: 1px; background: var(--rule);
  }
  .address {
    position: absolute;
    right: 34px; top: 170px;
    text-align: right;
    font-size: 16px;
    line-height: 1.35;
  }
  .person { position: absolute; left: 40px; top: 206px; }
  .person__name {
    font-weight: 600;
    font-size: 23px;
    color: var(--mint);
    letter-spacing: 0.5px;
  }
  .person__role { font-size: 17px; margin-top: -2px; }
  .contact { position: absolute; left: 40px; top: 280px; list-style: none; font-size: 17px; line-height: 1.5; }
  .contact li { display: flex; align-items: center; gap: 8px; }
  .contact svg { width: 16px; height: 16px; fill: var(--mint); flex: none; }
</style>
</head>
<body>

<section class="card card--back" aria-label="Card back">
  <div class="leaf-decor" aria-hidden="true"></div>
  <div class="brand">
    <span class="brand__mark" aria-hidden="true"></span>
    <span class="brand__name">Cedar and Willow<br>Massage Studio</span>
  </div>
  <div class="follow">
    <div class="follow__rule"></div>
    <p class="follow__label">FOLLOW US ON</p>
    <div class="follow__links" aria-label="Social links">
      <span class="follow__dot"></span><span class="follow__dot"></span>
      <span class="follow__dot"></span><span class="follow__dot"></span>
    </div>
    <div class="follow__rule"></div>
  </div>
</section>

<section class="card card--front" aria-label="Card front">
  <div class="leaf-decor" aria-hidden="true"></div>
  <div class="brand">
    <span class="brand__mark" aria-hidden="true"></span>
    <span class="brand__name">Cedar and Willow<br>Massage Studio</span>
  </div>
  <div class="divider"></div>
  <address class="address" style="font-style:normal">482 Linden Ave. suite 210<br>Riverton, CA 90000</address>
  <div class="person">
    <p class="person__name">MARISOL VEGA</p>
    <p class="person__role">Massage Therapist</p>
  </div>
  <ul class="contact">
    <li>
      <svg viewBox="0 0 16 16" aria-hidden="true"><path d="M3 2h3l1 3-2 1a8 8 0 0 0 5 5l1-2 3 1v3a1 1 0 0 1-1 1A12 12 0 0 1 2 3a1 1 0 0 1 1-1z"/></svg>
      (555) 014-2270
    </li>
    <li>
      <svg viewBox="0 0 16 16" aria-hidden="true"><path d="M1 3h14v10H1z M2 4l6 5 6-5" stroke="#1e1e1e" stroke-width="1"/></svg>
      hello@cedarandwillow.example
    </li>
  </ul>
</section>

</body>
</html>
```